Business Cards Needed for Innovative Healthcare Marketing Company

We are a marketing company focused on healthcare. Our company is all about rebranding yourself renewing your image and generating results. The phoenix stands for "reborn" or "rising" which we provide new brands for our clients we take their old brands and renew it with creativity and innovation. I am looking for a business card with color dimension. I have attached an example of a card I think has the look and feel of what I am trying to accomplish. I like that the card example has black and grey font colors, I like the font placement and the small logo, I really like the use of the colors on the right those are the colors of my logo. My logo is phoenix so maybe incorporating flames similar to that design. I would like the back a solid color maybe red with an opaque version of the logo and website. As a marketing company I am always open to creative liberty!

Target Market(s)

Doctors and business professionals.

Industry/Entity Type

Marketing

Contact Information for Business Card

Valcorne Health Care Marketing
Marla Tenwick- CEO
#(512)638-2974
email-marla@valcorne.com
website- valcorne.com

Font styles to use
Sans Serif

Colors
ec1f27
f37122
ffc214
fbed22
fbf289
f04a50

Requirements
Must have
• The logo and required information
Nice to have
• icons by the information
Should not have
• child like font

```html
<!DOCTYPE html>
<html lang="en">
<head>
<meta charset="utf-8">
<title>Valcorne Health Care Marketing – Business Card</title>
<link rel="stylesheet" href="https://fonts.googleapis.com/css2?family=Roboto:wght@300;400;700&display=swap">
<style>
  :root {
    --stage: #3b3b3b;
    --brand-red: #a8242a;
    --brand-red-deep: #8f1c22;
    --flame-orange: #f37122;
    --flame-gold: #f7a21b;
    --paper: #ffffff;
    --ink-soft: #c4474b;
  }
  * { margin: 0; padding: 0; box-sizing: border-box; }
  html, body {
    width: 1200px; height: 950px; overflow: hidden;
    background: var(--stage);
    font-family: "Roboto", Arial, sans-serif;
  }
  .card {
    position: absolute;
    width: 600px; height: 343px;
    border-radius: 4px;
    overflow: hidden;
    box-shadow: 0 14px 30px rgba(0,0,0,.45);
  }
  /* Back */
  .card--back {
    left: 100px; top: 80px;
    background: linear-gradient(135deg, var(--brand-red) 0%, var(--brand-red-deep) 100%);
    color: var(--paper);
  }
  .back-brand {
    position: absolute; left: 150px; top: 105px;
    display: flex; align-items: center; gap: 18px;
  }
  .brand-dot {
    width: 58px; height: 58px; border-radius: 50%;
    border: 2px solid currentColor;
    flex: none;
  }
  .brand-name {
    font-weight: 300;
    text-transform: uppercase;
    line-height: 1.1;
  }
  .brand-name .primary { display: block; font-size: 40px; letter-spacing: 1px; }
  .brand-name .secondary { display: block; font-size: 13px; letter-spacing: 1.5px; }
  .back-web {
    position: absolute; left: 0; right: 0; top: 238px;
    text-align: center;
    font-size: 15px; letter-spacing: 5px;
  }
  /* Front */
  .card--front { left: 500px; top: 520px; background: var(--paper); }
  .card--front .wave { position: absolute; inset: 0; width: 100%; height: 100%; }
  .front-brand {
    position: absolute; left: 170px; top: 58px;
    display: flex; align-items: center; gap: 14px;
    color: var(--ink-soft);
  }
  .front-brand .brand-dot { width: 48px; height: 48px; border-color: var(--flame-orange); }
  .front-brand .primary { font-size: 34px; }
  .front-brand .secondary { font-size: 11px; }
  .person {
    position: absolute; left: 250px; top: 218px;
    text-align: center; width: 190px;
  }
  .person-name {
    color: var(--flame-gold);
    font-weight: 700; font-size: 19px; text-transform: uppercase;
    white-space: nowrap;
  }
  .person-role {
    color: var(--paper); font-size: 13px;
    border-top: 1px solid rgba(255,255,255,.8);
    margin-top: 4px; padding-top: 3px;
  }
  .contacts {
    position: absolute; left: 28px; bottom: 26px;
    list-style: none; color: var(--paper); font-size: 15px;
  }
  .contacts li { display: flex; align-items: center; gap: 9px; margin-top: 6px; }
  .contacts svg { width: 14px; height: 14px; fill: var(--flame-gold); }
  .front-web {
    position: absolute; right: 24px; top: 190px;
    color: var(--paper); font-size: 14px;
  }
</style>
</head>
<body>
  <section class="card card--back" aria-label="Card back">
    <div class="back-brand">
      <span class="brand-dot"></span>
      <span class="brand-name"><span class="primary">Valcorne</span><span class="secondary">Health Care Marketing</span></span>
    </div>
    <p class="back-web">www.valcorne.com</p>
  </section>

  <section class="card card--front" aria-label="Card front">
    <svg class="wave" viewBox="0 0 600 343" preserveAspectRatio="none" aria-hidden="true">
      <path d="M0,200 C90,240 180,222 300,160 C400,108 500,60 600,30 L600,343 L0,343 Z" fill="var(--flame-orange)"/>
      <path d="M0,211 C90,251 180,233 300,171 C400,119 500,71 600,41 L600,343 L0,343 Z" fill="var(--paper)"/>
      <path d="M0,216 C90,256 180,238 300,176 C400,124 500,76 600,46 L600,343 L0,343 Z" fill="var(--brand-red)"/>
    </svg>
    <div class="front-brand">
      <span class="brand-dot"></span>
      <span class="brand-name"><span class="primary">Valcorne</span><span class="secondary">Health Care Marketing</span></span>
    </div>
    <div class="person">
      <p class="person-name">Marla Tenwick</p>
      <p class="person-role">CEO</p>
    </div>
    <p class="front-web">www.valcorne.com</p>
    <ul class="contacts">
      <li><svg viewBox="0 0 24 24" aria-hidden="true"><path d="M6.6 10.8a15.1 15.1 0 0 0 6.6 6.6l2.2-2.2c.3-.3.7-.4 1-.2 1.1.4 2.3.6 3.6.6.6 0 1 .4 1 1V20c0 .6-.4 1-1 1A17 17 0 0 1 3 4c0-.6.4-1 1-1h3.5c.6 0 1 .4 1 1 0 1.3.2 2.5.6 3.6.1.3 0 .7-.2 1z"/></svg>(512)638-2974</li>
      <li><svg viewBox="0 0 24 24" aria-hidden="true"><path d="M2 5h20v14H2z M2 5l10 8 10-8" stroke="var(--brand-red)" stroke-width="1.5"/></svg>marla@valcorne.com</li>
    </ul>
  </section>
</body>
</html>
```